Single-sided business card for restaurant velmora with new logo made on this site

Business card options with new logo including restaurant name, address, phone number and website. This business card is single-sided only and will be presented at the hostess desk for clients to take. I would like to see options based on a cream card background, a white card background, a yellow card background and a burgundy colored background. It needs to be elegant and traditional.

Target Market(s)

local and international crowd

Industry/Entity Type

restaurant

Contact Information for Business Card

address, website and phone number

Font styles to use
Serif

Colors
EE7325
F08F49
F5BC92
FAE3D3
FDF4ED

Requirements
Must have
• new logo, address, phone number, website
Should not have
• more than three colors

```html
<!DOCTYPE html>
<html lang="es">
<head>
<meta charset="utf-8">
<title>Velmora — Tarjeta de presentación</title>
<link rel="stylesheet" href="https://fonts.googleapis.com/css2?family=Cinzel:wght@500&family=Crimson+Pro:wght@400;700&display=swap">
<style>
  :root{
    --stage:#2a2a2a;
    --cream:#fdf1d6;
    --cream-deep:#f7e2b8;
    --brown:#3d1e1e;
    --gold:#f2b12e;
    --ink:#2c1414;
    --text-light:#fbeedd;
  }
  *{margin:0;padding:0;box-sizing:border-box}
  html,body{width:1200px;height:800px;overflow:hidden;background:var(--stage)}
  .card{
    position:absolute;left:50px;top:89px;width:1100px;height:622px;
    background:var(--cream);overflow:hidden;
    font-family:"Crimson Pro",Georgia,serif;
  }
  .card__leaves{
    position:absolute;left:420px;top:60px;width:680px;height:562px;
    background:radial-gradient(ellipse at 65% 70%,var(--cream-deep) 0%,rgba(247,226,184,.5) 40%,rgba(253,241,214,0) 75%);
  }
  .card__panel{position:absolute;inset:0;width:1100px;height:622px}
  .contact{position:absolute;left:48px;top:348px;color:var(--text-light)}
  .contact__name,.contact__label{font-weight:700;font-size:25px;line-height:30px}
  .contact__line{font-size:24px;line-height:31px}
  .contact__label{margin-top:12px}
  .contact__phone{font-size:29px;line-height:34px;display:flex;align-items:center;gap:10px}
  .contact__phone svg{width:22px;height:22px}
  .contact__web{font-size:23px;line-height:30px;margin-top:4px;letter-spacing:.3px}
  .brand{position:absolute;left:660px;top:119px;width:310px;text-align:center}
  .brand__mark{width:190px;height:190px;margin:0 auto;background:var(--gold)}
  .brand__name{
    font-family:"Cinzel",Georgia,serif;font-weight:500;font-size:56px;
    letter-spacing:9px;color:var(--ink);margin-top:36px;line-height:1;padding-left:9px;
  }
  .brand__since{
    display:flex;align-items:center;justify-content:center;gap:14px;margin-top:16px;
    font-family:"Cinzel",Georgia,serif;font-size:13px;color:var(--ink);letter-spacing:1px;
  }
  .brand__since::before,.brand__since::after{content:"";width:68px;height:2px;background:var(--gold)}
</style>
</head>
<body>
  <main class="card">
    <div class="card__leaves" role="img" aria-label="Faint decorative agave leaves in soft cream tones"></div>

    <svg class="card__panel" viewBox="0 0 1100 622" aria-hidden="true">
      <path d="M0,0 H90 C70,130 330,300 440,420 C525,515 548,590 594,622 H0 Z" fill="var(--gold)"/>
      <path d="M0,0 H86 C66,130 324,300 433,420 C516,515 536,590 582,622 H0 Z" fill="#ffffff"/>
      <path d="M0,0 H84 C62,130 320,300 429,420 C512,515 532,590 578,622 H0 Z" fill="var(--brown)"/>
    </svg>

    <section class="contact">
      <p class="contact__name">Restaurant Velmora</p>
      <p class="contact__line">Jacaranda 415,</p>
      <p class="contact__line">Bahías de Lunamar</p>
      <p class="contact__line">Costa Verde CP 48210</p>
      <p class="contact__label">Reservaciones</p>
      <p class="contact__phone">
        <svg viewBox="0 0 24 24" fill="none" stroke="currentColor" stroke-width="1.6"><path d="M5 3h4l2 5-2.5 1.5a11 11 0 0 0 6 6L16 13l5 2v4a2 2 0 0 1-2 2A16 16 0 0 1 3 5a2 2 0 0 1 2-2z"/></svg>
        555-014-2290
      </p>
      <p class="contact__web">www.velmora.com.mx</p>
    </section>

    <section class="brand">
      <div class="brand__mark"></div>
      <p class="brand__name">VELMORA</p>
      <p class="brand__since">DESDE 1999</p>
    </section>
  </main>
</body>
</html>
```